Business Card Design for Occupational Medicine Start Up Company

We need to design a professional business card. We are a healthcare company providing occupational medicine services to blue collar industries. We are professional, efficient and high quality service providers.

Target Market(s)

Blue Collar Industry: Shipbuilding, Ports, Trucking Companies; The Executives and Safety Officers for these companies

Industry/Entity Type

Healthcare

Contact Information for Business Card

Logo, Name, Title, Email, Phone

Other font styles liked:
• Please match our Brand Guide

Requirements
Must have
• Our Company Colors and Logo

```html
<!DOCTYPE html>
<html lang="en">
<head>
<meta charset="utf-8">
<title>Keelbright Business Card</title>
<link rel="stylesheet" href="https://fonts.googleapis.com/css2?family=Montserrat:wght@600;700&family=Roboto:wght@400&display=swap">
<style>
  :root {
    --navy: #2b3590;
    --navy-deep: #232c7f;
    --orange: #f2ae4c;
    --sky: #2aa7e0;
    --white: #ffffff;
    --backdrop: #e9eaee;
  }
  html, body {
    margin: 0;
    width: 1200px;
    height: 912px;
    overflow: hidden;
    background: var(--backdrop);
  }
  .stage {
    position: relative;
    width: 1200px;
    height: 912px;
  }
  .card {
    position: absolute;
    left: 250px;
    width: 700px;
    height: 400px;
    overflow: hidden;
    box-shadow: 0 6px 18px rgba(0,0,0,.18);
  }
  .card-front { top: 36px; background: var(--navy); }
  .card-back { top: 476px; background: var(--white); }

  .front-pattern {
    position: absolute;
    inset: 0;
    background: linear-gradient(135deg, #3440a6 0%, var(--navy) 50%, var(--navy-deep) 100%);
  }
  .brand {
    position: absolute;
    display: flex;
    align-items: center;
    gap: 12px;
    font-family: "Montserrat", sans-serif;
    font-weight: 700;
    letter-spacing: 1px;
    white-space: nowrap;
  }
  .brand-dot {
    border-radius: 50%;
    flex: none;
  }
  .front-brand {
    left: 50%;
    top: 50%;
    transform: translate(-50%, -50%);
    color: var(--white);
    font-size: 38px;
  }
  .front-brand .brand-dot { width: 40px; height: 40px; background: var(--sky); }

  .back-brand {
    left: 60px;
    top: 82px;
    color: var(--navy);
    font-size: 36px;
  }
  .back-brand .brand-dot { width: 48px; height: 48px; background: var(--sky); }

  .accent-band {
    position: absolute;
    left: 560px; top: 118px;
    width: 140px; height: 100px;
    background: var(--orange);
  }
  .contact-band {
    position: absolute;
    left: 0; top: 218px;
    width: 700px; height: 182px;
    background: var(--navy);
  }
  .accent-disc {
    position: absolute;
    left: 505px; top: 128px;
    width: 130px; height: 130px;
    border-radius: 50%;
    background: var(--navy);
    border: 8px solid var(--white);
    box-sizing: border-box;
  }
  .person {
    position: absolute;
    left: 60px; top: 236px;
    color: var(--white);
    font-family: "Roboto", sans-serif;
  }
  .person-name {
    margin: 0;
    font-family: "Montserrat", sans-serif;
    font-weight: 700;
    font-size: 28px;
    color: var(--orange);
    letter-spacing: .5px;
  }
  .person-title {
    margin: 2px 0 16px;
    font-size: 17px;
  }
  .contact-list {
    list-style: none;
    margin: 0; padding: 0;
    font-size: 16px;
    line-height: 25px;
  }
  .contact-list li { display: flex; align-items: center; gap: 8px; }
  .contact-icon { width: 14px; height: 14px; flex: none; }
</style>
</head>
<body>
<main class="stage">
  <section class="card card-front" aria-label="Card front">
    <div class="front-pattern" role="img" aria-label="Repeating embossed brand pattern in deep blue"></div>
    <div class="brand front-brand">
      <span class="brand-dot"></span>
      <span class="brand-name">KEELBRIGHT</span>
    </div>
  </section>

  <section class="card card-back" aria-label="Card back">
    <div class="brand back-brand">
      <span class="brand-dot"></span>
      <span class="brand-name">KEELBRIGHT</span>
    </div>
    <div class="accent-band"></div>
    <div class="contact-band"></div>
    <div class="accent-disc"></div>
    <div class="person">
      <p class="person-name">DANIEL HART</p>
      <p class="person-title">Director</p>
      <ul class="contact-list">
        <li>
          <svg class="contact-icon" viewBox="0 0 24 24"><path fill="#f2ae4c" d="M6.6 10.8a15.5 15.5 0 0 0 6.6 6.6l2.2-2.2a1 1 0 0 1 1-.25 11.4 11.4 0 0 0 3.6.57 1 1 0 0 1 1 1V20a1 1 0 0 1-1 1A17 17 0 0 1 3 4a1 1 0 0 1 1-1h3.5a1 1 0 0 1 1 1c0 1.25.2 2.45.57 3.57a1 1 0 0 1-.25 1z"/></svg>
          <span>(555)014 2231</span>
        </li>
        <li>
          <svg class="contact-icon" viewBox="0 0 24 24"><rect x="2" y="5" width="20" height="14" rx="1" fill="#f2ae4c"/><path d="M2 6l10 7 10-7" fill="none" stroke="#2b3590" stroke-width="2"/></svg>
          <span>info@keelbrighthealth.com</span>
        </li>
        <li>
          <svg class="contact-icon" viewBox="0 0 24 24"><circle cx="12" cy="12" r="10" fill="#f2ae4c"/><path d="M2 12h20M12 2c3 3 3 17 0 20M12 2c-3 3-3 17 0 20" fill="none" stroke="#2b3590" stroke-width="1.5"/></svg>
          <span>www.keelbrighthealth.com</span>
        </li>
      </ul>
    </div>
  </section>
</main>
</body>
</html>
```